Fresh Dwelling Tract Guide needs a new Landing Page

I like to get a landing page or website with 2-3 pages to help target home buyers who are looking to buy homes from builders such as TW Residences, Morvik, P.L. Fennick, etc. The landing page/website to be non-cluttered and be able to explain to home buyers that there are many benefits to include me as their buyer's agent when they buy a brand new home from any builders.
I may want to incorporate a short explanation video (animated) on the landing page and then for the viewer to click on a button that will take them to another page where they can search for new homes from different builders.
Target Market(s)
Home buyers looking to buy brand new home from builders such as TW Residences, Morvik, P.L. Fennick, etc.
Industry/Entity Type
Real Estate
Number of Pages Required
2 page
Font styles to use
Requirements
Must have
- The landing page may have the explanation video at the bottom of the landing page (scrolled down) or there may be a CALL TO ACTION button that takes the viewer to the 2nd page to watch the explanation video. Once they watched the explanation video and are still interested, they can click on another CALL TO ACTION button that will take them to another website that they will be able to search for all the available new homes and register their contact information.
Should not have
- No clutters and no dark colors.

```html
<!DOCTYPE html>
<html lang="en">
<head>
<meta charset="utf-8">
<title>Fresh Dwelling Tract Guide</title>
<link href="https://fonts.googleapis.com/css2?family=Lato:wght@400;700;900&family=Open+Sans:wght@400&display=swap" rel="stylesheet">
<style>
  :root {
    --sky-top: #4f8fd0;
    --sky-mid: #7fb0dc;
    --sky-haze: #a9c9e2;
    --shore: #6fb8c4;
    --water: #22aabd;
    --water-deep: #178fa6;
    --shade: rgba(20, 50, 80, 0.16);
    --footer-bg: rgba(16, 72, 92, 0.62);
    --white: #ffffff;
    --footer-text: #e6f0f4;
    --accent: #8dc63f;
    --icon-dark: #1b2a3a;
  }
  * { margin: 0; padding: 0; box-sizing: border-box; }
  html, body { width: 1200px; height: 768px; overflow: hidden; }
  body { font-family: "Lato", sans-serif; color: var(--white); }
  .hero { position: relative; width: 1200px; height: 768px; overflow: hidden; }
  .hero-backdrop {
    position: absolute; inset: 0;
    background:
      linear-gradient(180deg, var(--sky-top) 0%, var(--sky-mid) 32%, var(--sky-haze) 50%, var(--shore) 57%, var(--water) 70%, var(--water-deep) 100%);
  }
  .hero-backdrop::after { content: ""; position: absolute; inset: 0; background: var(--shade); }
  .brand {
    position: absolute; left: 139px; top: 31px;
    font-weight: 400; color: var(--white); text-transform: uppercase; line-height: 1;
  }
  .brand-line-1 { display: block; font-size: 32px; letter-spacing: 0.3px; }
  .brand-line-2 { display: block; font-size: 19px; font-weight: 700; letter-spacing: 5.6px; margin-top: 6px; }
  .menu-toggle { position: absolute; left: 1001px; top: 38px; width: 40px; height: 24px; }
  .intro {
    position: absolute; left: 0; right: 0; top: 226px; text-align: center;
    text-shadow: 0 1px 6px rgba(10, 40, 70, 0.25);
  }
  .play-button { display: block; margin: 0 auto 0 calc(50% - 29px); width: 64px; height: 64px; }
  .intro-kicker { font-weight: 700; font-size: 36px; margin-top: 18px; line-height: 1; text-transform: uppercase; }
  .intro-title { font-weight: 700; font-size: 58px; line-height: 1; margin-top: 2px; text-transform: uppercase; }
  .cta {
    position: absolute; left: 454px; top: 422px; width: 303px; height: 57px;
    background: var(--accent); border-radius: 29px;
    display: flex; align-items: center; justify-content: center; gap: 8px;
    font-weight: 400; font-size: 23px; color: var(--white); text-decoration: none; text-transform: uppercase;
  }
  .site-footer {
    position: absolute; left: 0; right: 0; bottom: 0; height: 62px;
    background: var(--footer-bg);
    display: flex; align-items: center; justify-content: center;
    font-family: "Open Sans", sans-serif; font-size: 14.5px; color: var(--footer-text);
  }
</style>
</head>
<body>
<main class="hero">
  <div class="hero-backdrop" role="img" aria-label="Bright aerial view of a sunny waterfront marina with yachts, turquoise water and high-rise condo towers under a blue sky with white clouds"></div>

  <div class="brand">
    <span class="brand-line-1">Fresh Dwelling</span>
    <span class="brand-line-2">Tract Guide</span>
  </div>

  <svg class="menu-toggle" viewBox="0 0 40 24" aria-label="Menu">
    <rect x="0" y="0" width="40" height="3" fill="#fff"/>
    <rect x="0" y="10" width="40" height="3" fill="#fff"/>
    <rect x="0" y="21" width="40" height="3" fill="#fff"/>
  </svg>

  <section class="intro">
    <svg class="play-button" viewBox="0 0 64 64" role="img" aria-label="Play the short animated video on the benefits of having a buyer's agent when buying a new home from a builder">
      <circle cx="32" cy="32" r="30.5" fill="none" stroke="#fff" stroke-width="2.5"/>
      <circle cx="32" cy="32" r="26" fill="#fff"/>
      <path d="M26 21 L43 32 L26 43 Z" fill="var(--icon-dark)"/>
    </svg>
    <h2 class="intro-kicker">Welcome to Fresh Dwelling</h2>
    <h1 class="intro-title">Tract Guide</h1>
  </section>

  <a class="cta" href="#">
    <svg width="21" height="21" viewBox="0 0 20 20" aria-hidden="true">
      <circle cx="8" cy="8" r="6" fill="none" stroke="#fff" stroke-width="3"/>
      <path d="M12.5 12.5 L18 18" stroke="#fff" stroke-width="3.5" stroke-linecap="round"/>
    </svg>
    Search for Homes
  </a>

  <footer class="site-footer">© 2018 Company Name&nbsp; All right reserved</footer>
</main>
</body>
</html>
```